We’re a real estate firm that has landed a big builder in a neighboring state. Our branding needs...

We are a real estate firm who represents various builders along with doing resale here in Oregon. Our firm is growing to represent a big builder in Washington State and we’ll have another 40 brokers on our team. We need rebranding. As in, a new logo ( the house logo we have now looks cartoonish, hate it). We need new cards, something to really stand out. I’ve been thinking of using those NFC cards from ZEP or the ones with the seam color. I likely want two or three designs, a darker (as in a background color of black or grey) , a light one ( again I mean background color) and a credit card style (either plastic w an embossed name/number on front, or metal ). I’m thinking dark background for cc, or silver if it’s metal. That’s my thoughts, but you are the artists, so maybe you have an idea I haven’t considered. Our colors were black and red, but we don’t have to stick to that. Just nothing too busy. Oh, and we are typically representing the local, higher quality builders in our area (just below custom), but not national. Subdivisions are near the Kell Varney, Brisco, and Thornfield Crest sites. We are super excited, but without a lot of time to change the “look” of our brokerage. So I’ll be deciding and moving forward within 24 hours tops. Our name is Real Estate Summit Alliance ( we cant change the name because of timeline and business license) Thank you!

Industry/Entity Type

Real Estate

Contact Information for Business Card

The usual. Name of firm. Name of cardholder. Contact info.

Font styles to use
Serif
Sans Serif

Colors

Designer to choose colors to be used in the design.

Requirements
Must have
• A sleek or simple look. I included photos of cards with stylistic attributes we like. Thank you
Nice to have
• We really like the black backgrounds. With foil or embossed detail. We also like the black on black. Matte black card with raised shiny black detail. But still eye catching.
Should not have
• No ornate or busy looking style. We don’t want anything cluttered.

```html
<!DOCTYPE html>
<html lang="en">
<head>
<meta charset="utf-8">
<title>Real Estate Summit Alliance – Business Cards</title>
<link rel="stylesheet" href="https://fonts.googleapis.com/css2?family=Questrial&family=Open+Sans:wght@400;600&display=swap">
<style>
  :root {
    --backdrop: #2a2a2b;
    --card-light: #ececec;
    --card-grey: #7b7d81;
    --navy: #10305f;
    --slate: #838588;
    --ink: #1c1c1c;
    --rule: #a9a9a9;
    --white: #ffffff;
    --pale-text: #d4d7dc;
  }
  * { box-sizing: border-box; margin: 0; padding: 0; }
  html, body { width: 1200px; height: 1200px; overflow: hidden; }
  body { background: var(--backdrop); position: relative; font-family: "Open Sans", Arial, sans-serif; }

  .card { position: absolute; top: 310px; height: 594px; }
  .card--front { left: 234px; width: 364px; background: var(--card-light); text-align: center; }
  .card--back { left: 627px; width: 369px; background: var(--card-grey); overflow: hidden; }

  /* Front */
  .brand-mark { width: 22px; height: 22px; background: var(--navy); margin: 92px auto 0; }
  .brand-name {
    margin-top: 22px; font-family: "Questrial", Arial, sans-serif; color: var(--navy);
    font-size: 38px; line-height: 40px; letter-spacing: -0.3px;
  }
  .brand-name span { display: block; font-size: 19px; letter-spacing: 2.6px; line-height: 26px; }

  .holder { position: absolute; top: 340px; left: 0; right: 0; }
  .holder-name { font-family: "Questrial", Arial, sans-serif; font-weight: 400; color: var(--navy); font-size: 25px; line-height: 30px; letter-spacing: 0.3px; }
  .holder-role { font-size: 16px; color: var(--ink); line-height: 22px; }
  .rule { width: 208px; height: 1px; background: var(--rule); margin: 8px auto 10px; }
  .contact-list { list-style: none; font-size: 16.5px; line-height: 21.5px; color: var(--ink); }
  .contact-list b { color: var(--navy); font-weight: 600; }
  .contact-web { color: var(--navy); font-weight: 600; }
  .address { font-size: 16.5px; line-height: 21.5px; color: var(--ink); }

  /* Back */
  .back-band { position: absolute; left: 0; right: 0; top: 440px; bottom: 0; background: var(--navy); }
  .back-brand {
    position: absolute; top: 190px; left: 0; right: 0; text-align: center;
    font-family: "Questrial", Arial, sans-serif; color: var(--white); font-size: 34px; line-height: 38px;
  }
  .back-brand .brand-mark { background: var(--white); margin: 0 auto 20px; width: 26px; height: 26px; }
  .back-brand span { display: block; font-size: 17px; letter-spacing: 2.4px; line-height: 26px; }
  .back-web {
    position: absolute; top: 528px; left: 0; right: 0; text-align: center;
    color: var(--pale-text); font-weight: 600; font-size: 17px; letter-spacing: 0.3px;
  }
</style>
</head>
<body>
  <section class="card card--front">
    <div class="brand-mark"></div>
    <h1 class="brand-name">Real Estate<span>SUMMIT ALLIANCE</span></h1>

    <div class="holder">
      <h2 class="holder-name">Marcus Delane</h2>
      <p class="holder-role">Managing Director</p>
      <div class="rule"></div>
      <ul class="contact-list">
        <li><b>P:</b> 503-418 276 905</li>
        <li><b>M:</b> 503-418 276 905</li>
        <li><b>E:</b> info@resalliance.com</li>
        <li class="contact-web">www.resalliance.com</li>
      </ul>
      <div class="rule"></div>
      <p class="address">4820, Cedar Ridge Road<br>Portland, OR 97205.</p>
    </div>
  </section>

  <section class="card card--back">
    <div class="back-band"></div>
    <div class="back-brand">
      <div class="brand-mark"></div>
      Real Estate<span>SUMMIT ALLIANCE</span>
    </div>
    <p class="back-web">www.resalliance.com</p>
  </section>
</body>
</html>
```